Trade Show Design

Two, doublesided backdrops/one doublesided banner/one countertop. I have 3 sample pictures of the 3 items that we are purchasing and all the dimensions are listed on the file names.
website: www.brickwisestudio.net
We are a training center that teaches homeowner's how to do their own home renovations through in-person classes with hands-on training.
We are looking to update our tradeshow displays utilizing stock photos as our photos do not have high enough resolution. I have attached lots of example pictures to select from but some of my favourites that I want to use are over 10 MB so they won't upload. Will have to figure out a different way to upload. Our tagline is Build skills with your own hands. We also use words such as "learn to reno" or "practical, hands-on training". We want to use our current branding (pictures of our minivan are uploaded as well) and our color palette document and really show people what we are all about - classes that people can attend so they can learn to reno their home.
Updates

For the 2 backdrops, we would like them to either be stand-alone or together incase we go to a trade show and only have room for 1 of them. They are to be different designs, front and back but a continuous flow if we are to use them together. Again, I have to figure out how to upload additional pictures as some of the ones I want to use are larger. Thanks!

Same with the Banner that is also double-sided - this is to be a different design for the back and front. We want minimal wording on everything but we really want to showcase what we do so that people can figure it out quickly when they walk by our booth....we offer in-person class with hands-on training. Learn to do by doing. Like on our vehicle that I sent example pictures of, we can put a list of a few topics so that people can understand:
Renovation Topics:
Bathroom
Drywall
Flooring
Tiling
Basement
Framing
Plumbing
Baseboards
Feature Walls

Here is the link to the Vornel Box to additional photos.

https://files.vornelbox.net/shared/7QK4r_mz2-TX8LwBnPe5YuJsdA0fGhRkZ?view=open

Thanks,
Marla

```html
<!DOCTYPE html>
<html lang="en">
<head>
<meta charset="utf-8">
<title>Brickwise Studio — Trade Show Backdrops</title>
<link rel="stylesheet" href="https://fonts.googleapis.com/css2?family=Anton&family=Poppins:wght@400;600;700&display=swap">
<style>
  :root {
    --stage: #dde3ea;
    --teal: #2a6c78;
    --mustard: #dca43d;
    --cream: #e9e9b9;
    --sky: #b9d4ef;
    --olive-tint: #c8cb93;
    --white: #ffffff;
    --headline: "Anton", "Impact", sans-serif;
    --body: "Poppins", "Helvetica", sans-serif;
  }
  * { box-sizing: border-box; margin: 0; padding: 0; }
  html, body { width: 1200px; height: 900px; overflow: hidden; }
  body {
    background: var(--stage);
    font-family: var(--body);
    position: relative;
  }
  .backdrop {
    position: absolute;
    top: 217px;
    width: 560px;
    height: 466px;
    overflow: hidden;
    box-shadow: 0 10px 30px rgba(40, 60, 80, 0.15);
  }
  .backdrop--front { left: 28px; }
  .backdrop--back { left: 612px; }

  .grid { position: absolute; display: flex; }
  .tile {
    position: relative;
    display: flex;
    flex-direction: column;
    align-items: center;
    justify-content: center;
    text-align: center;
  }
  .tile--cream { background: var(--cream); color: var(--teal); }
  .tile--sky { background: var(--sky); color: var(--teal); }
  .tile--mustard { background: var(--mustard); color: var(--white); }
  .tile--teal { background: var(--teal); color: var(--white); }

  .photo { position: relative; }
  .photo--warm { background: linear-gradient(160deg, #e4ddd3, #b9a38a 70%, #7d6a55); }
  .photo--studio { background: linear-gradient(170deg, #9a8c7e, #5e5249 60%, #3a3532); }
  .photo--room { background: linear-gradient(150deg, #efece6, #d6cabd 60%, #a48c72); }
  .photo--shop { background: linear-gradient(160deg, #a98e76, #7a6453 55%, #4a4340); }
  .photo--ceiling { background: linear-gradient(170deg, #f3f1ee, #e2d9d2 60%, #b7867a); }
  .photo--floor { background: linear-gradient(160deg, #c9c6c2, #8a7e78 55%, #3e4a5e); }

  .topic-icon { width: 34px; height: 34px; margin-bottom: 10px; }
  .topic-list {
    font-weight: 700;
    font-size: 11.5px;
    line-height: 1.4;
    letter-spacing: 0.01em;
    text-transform: uppercase;
  }

  .brand { display: flex; flex-direction: column; align-items: flex-start; text-align: left; }
  .brand__row { display: flex; align-items: center; gap: 5px; white-space: nowrap; }
  .brand__mark { width: 11px; height: 11px; background: var(--mustard); flex: none; }
  .brand__name {
    font-weight: 700;
    font-size: 13px;
    color: var(--teal);
    line-height: 1.1;
    white-space: nowrap;
  }
  .brand__tagline {
    font-weight: 400;
    font-size: 7.5px;
    color: var(--teal);
    margin-top: 4px;
    white-space: nowrap;
  }

  .headline {
    font-family: var(--headline);
    font-weight: 400;
    line-height: 1;
  }

  .url-pill {
    display: inline-flex;
    align-items: center;
    height: 24px;
    background: var(--teal);
    color: var(--white);
    border-radius: 12px 4px 4px 12px;
    padding-right: 10px;
    font-size: 9px;
    font-weight: 400;
    white-space: nowrap;
  }
  .url-pill__dot {
    width: 24px;
    height: 24px;
    border-radius: 50%;
    background: var(--mustard);
    display: flex;
    align-items: center;
    justify-content: center;
    margin-right: 7px;
  }
  .url-pill__dot svg { width: 10px; height: 10px; }

  /* front backdrop */
  .front-row { left: 0; width: 560px; }
  .front-row--top { top: 0; height: 161px; }
  .front-row--mid { top: 161px; height: 163px; }
  .front-row--bottom { top: 324px; height: 142px; }
  .learn-reno .headline { font-size: 50px; letter-spacing: 0.005em; }
  .learn-reno__swoosh { width: 110px; height: 18px; margin-top: 2px; margin-left: 40px; }

  /* back backdrop */
  .intro-column {
    position: absolute;
    left: 0; top: 0;
    width: 226px;
    height: 466px;
    overflow: hidden;
  }
  .intro-column__photo {
    position: absolute;
    inset: 0;
    background: linear-gradient(170deg, #d2d39f, var(--olive-tint) 45%, #a9ab78);
  }
  .intro-column__content {
    position: absolute;
    inset: 0;
    padding: 46px 16px 0 16px;
  }
  .intro-column .brand { margin-left: 24px; }
  .practical { margin-top: 58px; color: var(--teal); font-size: 40px; }
  .practical__hands {
    display: inline-block;
    background: var(--mustard);
    color: var(--white);
    padding: 4px 10px 4px 8px;
    transform: rotate(-3deg);
    margin: 4px 0 6px;
    font-size: 34px;
  }
  .practical__line { display: block; }
  .practical__swoosh { width: 80px; height: 10px; margin-left: 14px; }
  .intro-column .url-pill { position: absolute; left: 28px; bottom: 42px; }

  .back-grid { position: absolute; left: 226px; top: 0; width: 334px; height: 466px; }
  .back-grid .grid { left: 0; width: 334px; }
  .back-row--top { top: 0; height: 158px; }
  .back-row--mid { top: 158px; height: 150px; }
  .back-row--bottom { top: 308px; height: 158px; }
  .back-grid .topic-list { font-size: 10px; }
  .back-grid .topic-icon { width: 30px; height: 30px; }
</style>
</head>
<body>

<svg width="0" height="0" style="position:absolute" aria-hidden="true">
  <defs>
    <symbol id="icon-drill" viewBox="0 0 40 40">
      <rect x="6" y="6" width="22" height="12" rx="3" fill="currentColor"/>
      <rect x="28" y="10" width="4" height="4" fill="currentColor"/>
      <rect x="32" y="11" width="7" height="2" fill="currentColor"/>
      <rect x="11" y="18" width="9" height="13" fill="currentColor"/>
      <rect x="9" y="31" width="13" height="6" rx="1.5" fill="currentColor"/>
    </symbol>
    <symbol id="icon-toolbox" viewBox="0 0 40 40">
      <rect x="10" y="3" width="5" height="14" fill="currentColor"/>
      <rect x="8" y="2" width="9" height="4" rx="1" fill="currentColor"/>
      <rect x="22" y="5" width="4" height="12" fill="currentColor"/>
      <circle cx="24" cy="5" r="4" fill="none" stroke="currentColor" stroke-width="2"/>
      <rect x="4" y="17" width="32" height="18" rx="2" fill="currentColor"/>
      <rect x="16" y="24" width="8" height="4" rx="1" fill="#ffffff" opacity="0.9"/>
    </symbol>
    <symbol id="icon-shower" viewBox="0 0 40 40">
      <path d="M6 38 V14 a8 8 0 0 1 16 0" fill="none" stroke="currentColor" stroke-width="3.5"/>
      <path d="M14 14 h16 a8 8 0 0 0 -16 0z" fill="currentColor" transform="rotate(30 22 14)"/>
      <g stroke="currentColor" stroke-width="1.6" stroke-linecap="round">
        <line x1="18" y1="22" x2="16" y2="28"/><line x1="22" y1="23" x2="20" y2="31"/>
        <line x1="26" y1="22" x2="25" y2="30"/><line x1="30" y1="20" x2="31" y2="27"/>
        <line x1="33" y1="17" x2="36" y2="23"/><line x1="21" y1="33" x2="20" y2="36"/>
        <line x1="26" y1="33" x2="26" y2="37"/>
      </g>
    </symbol>
    <symbol id="icon-pointer" viewBox="0 0 10 10">
      <path d="M2 1 L2 9 L4 7 L5.5 9.5 L7 8.8 L5.6 6.4 L8.5 6.2 Z" fill="#ffffff"/>
    </symbol>
  </defs>
</svg>

<!-- Front backdrop: Learn To Reno -->
<section class="backdrop backdrop--front" aria-label="Learn To Reno backdrop">
  <div class="grid front-row front-row--top">
    <div class="photo photo--warm" style="width:145px" role="img" aria-label="Photo of a smiling couple in work shirts and tool belts, one holding a cordless drill"></div>
    <div class="tile tile--cream" style="width:147px">
      <div class="brand">
        <div class="brand__row">
          <span class="brand__mark"></span>
          <span class="brand__name">Brickwise Studio</span>
        </div>
        <span class="brand__tagline">Build skills with your own hands.</span>
      </div>
    </div>
    <div class="photo photo--studio" style="width:146px" role="img" aria-label="Photo of a smiling woman in a plaid shirt swinging a hammer toward the viewer"></div>
    <div class="tile tile--mustard" style="width:122px">
      <svg class="topic-icon" style="color:var(--white)"><use href="#icon-drill"/></svg>
      <p class="topic-list">Drywall<br>Feature Walls<br>Framing</p>
    </div>
  </div>

  <div class="grid front-row front-row--mid">
    <div class="tile tile--cream" style="width:145px">
      <svg class="topic-icon" style="color:var(--teal)"><use href="#icon-shower"/></svg>
      <p class="topic-list">Tiling<br>Bathroom<br>Plumbing</p>
    </div>
    <div class="tile tile--teal learn-reno" style="width:293px">
      <h1 class="headline">Learn<br>To Reno</h1>
      <svg class="learn-reno__swoosh" viewBox="0 0 110 18" aria-hidden="true">
        <path d="M2 8 C40 4 80 3 106 4 C90 6 70 10 56 15" fill="none" stroke="var(--mustard)" stroke-width="2" stroke-linecap="round"/>
      </svg>
    </div>
    <div class="tile tile--sky" style="width:122px">
      <svg class="topic-icon" style="color:var(--teal)"><use href="#icon-toolbox"/></svg>
      <p class="topic-list">Flooring<br>Baseboards<br>Basement</p>
    </div>
  </div>

  <div class="grid front-row front-row--bottom">
    <div class="photo photo--room" style="width:196px" role="img" aria-label="Photo of a couple in a bright room under renovation holding tile and a paint roller"></div>
    <div class="tile tile--sky" style="width:174px">
      <span class="url-pill">
        <span class="url-pill__dot"><svg><use href="#icon-pointer"/></svg></span>
        brickwisestudio.net
      </span>
    </div>
    <div class="photo photo--shop" style="width:190px" role="img" aria-label="Photo of a woman in safety glasses and gloves using a cordless drill on wood"></div>
  </div>
</section>

<!-- Back backdrop: Practical, Hands-on Training -->
<section class="backdrop backdrop--back" aria-label="Practical, Hands-on Training backdrop">
  <div class="intro-column">
    <div class="intro-column__photo" role="img" aria-label="Olive-tinted photo of a person working on a woodworking project"></div>
    <div class="intro-column__content">
      <div class="brand">
        <div class="brand__row">
          <span class="brand__mark"></span>
          <span class="brand__name">Brickwise Studio</span>
        </div>
        <span class="brand__tagline">Build skills with your own hands.</span>
      </div>
      <h2 class="headline practical">
        <span class="practical__line">Practical,</span>
        <span class="practical__hands">Hands-on</span>
        <span class="practical__line">Training.</span>
      </h2>
      <svg class="practical__swoosh" viewBox="0 0 80 10" aria-hidden="true">
        <path d="M2 6 C30 3 55 3 78 4" fill="none" stroke="var(--mustard)" stroke-width="2" stroke-linecap="round"/>
      </svg>
    </div>
    <span class="url-pill">
      <span class="url-pill__dot"><svg><use href="#icon-pointer"/></svg></span>
      brickwisestudio.net
    </span>
  </div>

  <div class="back-grid">
    <div class="grid back-row--top">
      <div class="photo photo--ceiling" style="width:334px" role="img" aria-label="Photo of two people installing a ceiling light fixture together"></div>
    </div>
    <div class="grid back-row--mid">
      <div class="tile tile--teal" style="width:165px">
        <svg class="topic-icon" style="color:var(--white)"><use href="#icon-drill"/></svg>
        <p class="topic-list">Drywall<br>Feature Walls<br>Framing</p>
      </div>
      <div class="tile tile--cream" style="width:169px">
        <svg class="topic-icon" style="color:var(--teal)"><use href="#icon-toolbox"/></svg>
        <p class="topic-list">Flooring<br>Baseboards<br>Basement</p>
      </div>
    </div>
    <div class="grid back-row--bottom">
      <div class="photo photo--floor" style="width:165px" role="img" aria-label="Photo of a couple kneeling to lay laminate flooring planks"></div>
      <div class="tile tile--sky" style="width:169px">
        <svg class="topic-icon" style="color:var(--teal)"><use href="#icon-shower"/></svg>
        <p class="topic-list">Tiling<br>Bathroom<br>Plumbing</p>
      </div>
    </div>
  </div>
</section>

</body>
</html>
```